QuillVane needs a dashboard page designed

Redesign the dashboard shown in the provided images.

There are two images:
- dashboard.png
- dashboard-expanded.png

NOTE: The vocabulary navigation on the left will be a very long list of words 100s, so keep that in mind when you're designing both the vocab navigation and the expanded vocab popup.

In the dashboard.png picture, there needs to be a progress chart showing the word progress like the following: review 1(show it as completed) -> review 2(show the user they are here) -> review 3(unvisited) -> review 4(unvisited)

The do-not-design-this-page.png image is for your reference only. It is not to be designed. Use it to understand the overall look and feel of the website to help you create the best dashboard page possible.
Updates

Need extra days to review

Industry/Entity Type

Education English learning

Number of Pages Required

1 page

Requirements
Must have
• The main navigation and main header cannot change between pages. See the do-not-design page for the main navigateion and header.
Should not have
• Do not add a person profile. We will not have images of our users. Keep the icons in the main navigation as they are.

```html
<!DOCTYPE html>
<html lang="en">
<head>
<meta charset="utf-8">
<title>QuillVane – WordWise Tutor Dashboard</title>
<link href="https://fonts.googleapis.com/css2?family=Roboto:wght@400;500;700&display=swap" rel="stylesheet">
<style>
:root{
  --page:#d3d3d3;
  --navy:#1b3f63;
  --red:#8b1a1a;
  --side:#f4f8fc;
  --text:#555b62;
  --ink:#1f3550;
  --band:#f1f6fc;
  --bar-blue:#d6e6fb;
  --bar-green:#c4f7c0;
  --bar-yellow:#fdf78f;
  --bar-gray:#e3e3e3;
  --online:#2ecc40;
}
*{box-sizing:border-box;margin:0;padding:0}
html,body{width:961px;height:1200px;overflow:hidden;background:var(--page)}
body{font-family:"Roboto",sans-serif;color:var(--ink)}
.stage{position:absolute;left:0;top:0;width:1640px;height:2048px;transform:scale(.58598);transform-origin:0 0}
.screen{position:absolute;left:100px;width:1440px;height:900px;background:#fff;overflow:hidden}
.screen-main{top:88px}
.screen-popup{top:1060px}
.abs{position:absolute}
.brand{left:0;top:0;width:235px;height:64px;display:flex;align-items:center;padding-left:31px;font-size:24px;font-weight:700;color:var(--navy);letter-spacing:.3px}
.topbar-line{left:235px;top:63px;width:1205px;height:1px;background:#eef1f4}
.page-title{top:19px;font-size:19px;font-weight:500;color:var(--red)}
.avatar{left:1148px;top:10px;width:44px;height:44px;border-radius:50%;background:linear-gradient(135deg,#6b7d8c,#3a4a58)}
.online{left:1182px;top:9px;width:11px;height:11px;border-radius:50%;background:var(--online);border:2px solid #fff}
.email{left:1211px;top:22px;font-size:14px;color:var(--text)}
.gear{left:1392px;top:20px}
.main-nav{left:0;top:64px;width:235px;height:836px;background:var(--navy)}
.nav-item{position:absolute;left:0;width:235px;height:51px;display:flex;align-items:center;padding-left:18px;gap:14px;color:#fff;font-size:16px}
.nav-item.active{background:var(--red)}
.vocab-col{left:235px;top:64px;width:235px;height:836px;background:var(--side)}
.select{background:#fff;border:1px solid #e1e6ec;border-radius:3px;display:flex;align-items:center;justify-content:space-between;padding:0 12px;font-size:13px;color:var(--text)}
.expand-btn{left:122px;top:39px;width:100px;height:40px;border-radius:3px;background:var(--navy);color:#fff;font-size:14px;display:flex;align-items:center;justify-content:center;gap:6px}
.group-title{display:flex;align-items:center;gap:14px;font-size:16px;color:var(--ink)}
.group-title.current{color:var(--red)}
.word{font-size:14px;color:var(--text)}
.word.current{color:var(--red)}
.word-list{list-style:none}
.word-list li{height:26px;font-size:14px;color:var(--text);display:flex;align-items:center;gap:8px}
.word-list li::before{content:"›";font-size:15px;color:var(--ink)}
.reviews{left:528px;top:81px;width:888px;height:62px;background:var(--band);display:flex;justify-content:space-between;padding:10px 28px 0 30px}
.review b{display:block;font-weight:500;font-size:16px;color:var(--ink)}
.review span{font-size:12px;color:var(--text)}
.review span.now{color:var(--red)}
.word-head{font-size:20px;font-weight:500;color:var(--navy);display:flex;align-items:center;gap:8px}
.start-link{font-size:18px;font-weight:500;color:var(--navy);display:flex;align-items:center;gap:8px}
.para{width:890px;font-size:16px;line-height:29px;color:var(--text)}
.section-title{font-size:18px;font-weight:500;color:var(--navy)}
.legend{left:596px;width:770px;display:flex;justify-content:space-between;font-size:14px;color:var(--ink)}
.legend span{display:flex;align-items:center;gap:6px}
.legend i{width:11px;height:11px;border-radius:50%;display:inline-block}
.chart{left:500px}
.dim{left:0;top:0;width:1440px;height:900px;background:rgba(36,80,122,.86)}
.modal{left:478px;top:222px;width:484px;height:400px;background:var(--side);border-radius:18px}
.close{left:975px;top:206px;color:#fff;font-size:20px}
.start-btn{left:1027px;top:98px;width:389px;height:49px;background:var(--navy);border-radius:4px;display:flex;align-items:center;justify-content:center;gap:8px;color:#fff;font-size:18px;font-weight:500}
</style>
</head>
<body>
<div class="stage">

<!-- Dashboard -->
<section class="screen screen-main">
  <div class="abs brand">QuillVane</div>
  <div class="abs topbar-line"></div>
  <div class="abs page-title" style="left:527px">WORDWISE TUTOR</div>
  <div class="abs avatar" role="img" aria-label="User avatar"></div>
  <div class="abs online"></div>
  <div class="abs email">learner@quillvane.com</div>
  <svg class="abs gear" width="24" height="24" viewBox="0 0 24 24" fill="none" stroke="#1b3f63" stroke-width="2"><circle cx="12" cy="12" r="3"/><path d="M19.4 15a1.7 1.7 0 0 0 .3 1.8l.1.1a2 2 0 1 1-2.8 2.8l-.1-.1a1.7 1.7 0 0 0-1.8-.3 1.7 1.7 0 0 0-1 1.5V21a2 2 0 1 1-4 0v-.1a1.7 1.7 0 0 0-1.1-1.5 1.7 1.7 0 0 0-1.8.3l-.1.1a2 2 0 1 1-2.8-2.8l.1-.1a1.7 1.7 0 0 0 .3-1.8 1.7 1.7 0 0 0-1.5-1H3a2 2 0 1 1 0-4h.1a1.7 1.7 0 0 0 1.5-1.1 1.7 1.7 0 0 0-.3-1.8l-.1-.1a2 2 0 1 1 2.8-2.8l.1.1a1.7 1.7 0 0 0 1.8.3H9a1.7 1.7 0 0 0 1-1.5V3a2 2 0 1 1 4 0v.1a1.7 1.7 0 0 0 1 1.5 1.7 1.7 0 0 0 1.8-.3l.1-.1a2 2 0 1 1 2.8 2.8l-.1.1a1.7 1.7 0 0 0-.3 1.8V9a1.7 1.7 0 0 0 1.5 1H21a2 2 0 1 1 0 4h-.1a1.7 1.7 0 0 0-1.5 1z"/></svg>

  <nav class="abs main-nav">
    <div class="nav-item active" style="top:32px"><svg width="20" height="18" viewBox="0 0 20 18" fill="#fff"><path d="M10 1 1 9h3v8h4v-5h4v5h4V9h3z"/></svg>WordWise Tutor</div>
    <div class="nav-item" style="top:93px"><svg width="20" height="20" viewBox="0 0 20 20" fill="none" stroke="#fff" stroke-width="2"><circle cx="10" cy="10" r="8"/><path d="M10 5v5H7"/></svg>Daily English</div>
    <div class="nav-item" style="top:157px"><svg width="20" height="20" viewBox="0 0 20 20" fill="none" stroke="#fff" stroke-width="1.6"><rect x="3" y="1" width="14" height="18"/><path d="M6 5h2M11 5h2M6 9h2M11 9h2M6 13h2M11 13h2"/></svg>Business</div>
  </nav>

  <aside class="abs vocab-col">
    <div class="abs select" style="left:15px;top:39px;width:97px;height:40px">All <span>⌄</span></div>
    <div class="abs expand-btn">Expand <svg width="14" height="14" viewBox="0 0 14 14" fill="none" stroke="#fff" stroke-width="1.6"><path d="M8 1h5v5M13 1 6 8M11 8v5H1V3h5"/></svg></div>
    <div class="abs group-title current" style="left:17px;top:117px"><svg width="22" height="22" viewBox="0 0 22 22" fill="none" stroke="#8b1a1a" stroke-width="2.2"><path d="M3 11a8 8 0 1 0 2.5-5.8L3 7.5M3 3v4.5h4.5M11 7v4l3 2"/></svg>Short-Term Memory</div>
    <div class="abs word current" style="left:52px;top:155px">Grab</div>
    <div class="abs group-title" style="left:17px;top:203px"><svg width="22" height="22" viewBox="0 0 22 22" fill="#1b3f63"><rect x="5" y="1" width="12" height="20" rx="1"/><path d="M2 4h2v2H2zM2 9h2v2H2zM2 14h2v2H2zM18 4h2v2h-2zM18 9h2v2h-2zM18 14h2v2h-2z"/></svg>Working Memory</div>
    <ul class="abs word-list" style="left:55px;top:238px">
      <li>Cool Down</li><li>Crave</li><li>Fo for</li><li>Go To</li><li>In The Mood For</li><li>Sip</li><li>Soothing</li><li>Stick With</li><li>Throw In/Throw On</li>
    </ul>
    <div class="abs group-title" style="left:17px;top:501px"><svg width="20" height="22" viewBox="0 0 20 22" fill="#1b3f63"><path d="M5 9V6a5 5 0 0 1 10 0v3h-2.5V6a2.5 2.5 0 0 0-5 0v3z"/><rect x="3" y="9" width="14" height="11" rx="1"/></svg>Long-Term Memory</div>
    <div class="abs word" style="left:52px;top:540px">Give It A Try</div>
  </aside>

  <div class="abs reviews">
    <div class="review"><b>Review 01</b><span>Completed</span></div>
    <div class="review"><b>Review 02</b><span class="now">Prograss</span></div>
    <div class="review"><b>Review 03</b><span>Unvisited</span></div>
    <div class="review"><b>Review 04</b><span>Unvisited</span></div>
  </div>

  <div class="abs word-head" style="left:529px;top:194px">GRAB <svg width="20" height="20" viewBox="0 0 20 20" fill="#f5b700"><path d="M10 1l2.8 5.8 6.2.8-4.6 4.3 1.2 6.2L10 15l-5.6 3.1 1.2-6.2L1 7.6l6.2-.8z"/></svg></div>
  <div class="abs start-link" style="left:1058px;top:192px"><svg width="17" height="17" viewBox="0 0 18 18"><circle cx="9" cy="9" r="9" fill="#8b1a1a"/><path d="M7 5l6 4-6 4z" fill="#fff"/></svg>Start Vocabulary Review Exercise 3</div>
  <p class="abs para" style="left:529px;top:238px">The Word "Grab" Is Most Commonly Used As A Verb, Meaning To Take Something Quickly Or Suddenly. Imagine You're Running Late For School. You Don't Have Time For Breakfast, So You Quickly Grab An Apple From The Kitchen And Rush Out The Door. As You Reach The Bus Stop, Your Friend Waves And Says, "Hey! Let's Grab A Coffee Aller Class" Later, When You Sit Down, Your Phone Starts Ringing. You Grab It From Your Brag And Answer</p>

  <div class="abs section-title" style="left:526px;top:393px">LEARNING CURVE GRAPH</div>
  <svg class="abs chart" style="top:422px" width="920" height="270" viewBox="600 510 920 270" font-family="Roboto, sans-serif" font-size="10" fill="#333" text-anchor="middle">
    <path d="M628 560V773H1490" fill="none" stroke="#e6e6e6"/>
    <rect x="654" y="563" width="18" height="210" fill="var(--bar-blue)"/><rect x="683" y="585" width="18" height="188" fill="var(--bar-green)"/>
    <text x="662" y="536">18</text><text x="662" y="550">May</text><text x="692" y="578">12:00</text>
    <rect x="735" y="585" width="18" height="188" fill="var(--bar-gray)"/><rect x="764" y="606" width="18" height="167" fill="var(--bar-yellow)"/>
    <text x="744" y="562">19</text><text x="744" y="576">May</text><text x="773" y="600">12:00</text>
    <rect x="816" y="667" width="18" height="106" fill="var(--bar-blue)"/><rect x="845" y="602" width="18" height="171" fill="var(--bar-green)"/>
    <text x="824" y="643">20</text><text x="824" y="657">May</text><text x="854" y="596">12:00</text>
    <rect x="898" y="563" width="18" height="210" fill="var(--bar-yellow)"/><rect x="927" y="648" width="18" height="125" fill="var(--bar-gray)"/>
    <text x="907" y="543">21</text><text x="907" y="557">May</text><text x="936" y="639">12:00</text>
    <rect x="979" y="563" width="18" height="210" fill="var(--bar-blue)"/><rect x="1008" y="585" width="18" height="188" fill="var(--bar-gray)"/>
    <text x="988" y="540">22</text><text x="988" y="554">May</text><text x="1017" y="579">12:00</text>
    <rect x="1060" y="648" width="18" height="125" fill="var(--bar-green)"/><rect x="1089" y="617" width="18" height="156" fill="var(--bar-yellow)"/>
    <text x="1068" y="625">23</text><text x="1068" y="639">May</text><text x="1096" y="611">12:00</text>
    <rect x="1135" y="667" width="18" height="106" fill="var(--bar-blue)"/><rect x="1164" y="563" width="18" height="210" fill="var(--bar-green)"/>
    <text x="1144" y="646">24</text><text x="1144" y="660">May</text><text x="1173" y="555">12:00</text>
    <rect x="1208" y="563" width="18" height="210" fill="var(--bar-blue)"/><rect x="1237" y="624" width="18" height="149" fill="var(--bar-yellow)"/>
    <text x="1217" y="540">25</text><text x="1217" y="554">May</text><text x="1246" y="618">12:00</text>
    <rect x="1289" y="648" width="18" height="125" fill="var(--bar-gray)"/><rect x="1318" y="617" width="18" height="156" fill="var(--bar-green)"/>
    <text x="1298" y="626">26</text><text x="1298" y="640">May</text><text x="1327" y="610">12:00</text>
    <rect x="1364" y="667" width="18" height="106" fill="var(--bar-yellow)"/><rect x="1393" y="563" width="18" height="210" fill="var(--bar-gray)"/>
    <text x="1373" y="647">27</text><text x="1373" y="661">May</text><text x="1402" y="558">12:00</text>
    <rect x="1435" y="602" width="18" height="171" fill="var(--bar-green)"/><rect x="1464" y="667" width="18" height="106" fill="var(--bar-yellow)"/>
    <text x="1444" y="581">28</text><text x="1444" y="595">May</text><text x="1473" y="662">12:00</text>
  </svg>
  <div class="abs legend" style="top:714px">
    <span><i style="background:var(--bar-blue)"></i>Long Term Memory</span>
    <span><i style="background:var(--bar-green)"></i>Working Memory</span>
    <span><i style="background:var(--bar-yellow)"></i>Short Term Memory</span>
    <span><i style="background:var(--bar-gray)"></i>Forgotten Memory</span>
  </div>

  <div class="abs section-title" style="left:528px;top:772px">WORDWISE TUTOR LEAMING ANALYSIS</div>
  <p class="abs para" style="left:529px;top:811px">Lorem ipsum dolor sit amet, consectetur adipiscing elit, sed do eiusmod tempor incididunt ut labore et dolore magna aliqua. Ut enim ad minim veniam, quis nostrud exercitation ullamco laboris nisi ut aliquip</p>
</section>

<!-- Dashboard with expanded vocabulary -->
<section class="screen screen-popup">
  <div class="abs brand">QuillVane</div>
  <div class="abs topbar-line"></div>
  <div class="abs page-title" style="left:639px">WORDWISE TUTOR</div>
  <div class="abs avatar" role="img" aria-label="User avatar"></div>
  <div class="abs online"></div>
  <div class="abs email">learner@quillvane.com</div>
  <svg class="abs gear" width="24" height="24" viewBox="0 0 24 24" fill="none" stroke="#1b3f63" stroke-width="2"><circle cx="12" cy="12" r="3"/><path d="M19.4 15a1.7 1.7 0 0 0 .3 1.8l.1.1a2 2 0 1 1-2.8 2.8l-.1-.1a1.7 1.7 0 0 0-1.8-.3 1.7 1.7 0 0 0-1 1.5V21a2 2 0 1 1-4 0v-.1a1.7 1.7 0 0 0-1.1-1.5 1.7 1.7 0 0 0-1.8.3l-.1.1a2 2 0 1 1-2.8-2.8l.1-.1a1.7 1.7 0 0 0 .3-1.8 1.7 1.7 0 0 0-1.5-1H3a2 2 0 1 1 0-4h.1a1.7 1.7 0 0 0 1.5-1.1 1.7 1.7 0 0 0-.3-1.8l-.1-.1a2 2 0 1 1 2.8-2.8l.1.1a1.7 1.7 0 0 0 1.8.3H9a1.7 1.7 0 0 0 1-1.5V3a2 2 0 1 1 4 0v.1a1.7 1.7 0 0 0 1 1.5 1.7 1.7 0 0 0 1.8-.3l.1-.1a2 2 0 1 1 2.8 2.8l-.1.1a1.7 1.7 0 0 0-.3 1.8V9a1.7 1.7 0 0 0 1.5 1H21a2 2 0 1 1 0 4h-.1a1.7 1.7 0 0 0-1.5 1z"/></svg>

  <nav class="abs main-nav">
    <div class="nav-item active" style="top:32px"><svg width="20" height="18" viewBox="0 0 20 18" fill="#fff"><path d="M10 1 1 9h3v8h4v-5h4v5h4V9h3z"/></svg>WordWise Tutor</div>
    <div class="nav-item" style="top:93px"><svg width="20" height="20" viewBox="0 0 20 20" fill="none" stroke="#fff" stroke-width="2"><circle cx="10" cy="10" r="8"/><path d="M10 5v5H7"/></svg>Daily English</div>
    <div class="nav-item" style="top:157px"><svg width="20" height="20" viewBox="0 0 20 20" fill="none" stroke="#fff" stroke-width="1.6"><rect x="3" y="1" width="14" height="18"/><path d="M6 5h2M11 5h2M6 9h2M11 9h2M6 13h2M11 13h2"/></svg>Business</div>
  </nav>
  <aside class="abs vocab-col">
    <div class="abs select" style="left:15px;top:39px;width:97px;height:40px">All <span>⌄</span></div>
    <div class="abs expand-btn">Expand <svg width="14" height="14" viewBox="0 0 14 14" fill="none" stroke="#fff" stroke-width="1.6"><path d="M8 1h5v5M13 1 6 8M11 8v5H1V3h5"/></svg></div>
    <div class="abs group-title current" style="left:17px;top:117px"><svg width="22" height="22" viewBox="0 0 22 22" fill="none" stroke="#8b1a1a" stroke-width="2.2"><path d="M3 11a8 8 0 1 0 2.5-5.8L3 7.5M3 3v4.5h4.5M11 7v4l3 2"/></svg>Short-Term Memory</div>
    <div class="abs word current" style="left:52px;top:155px">Grab</div>
    <div class="abs group-title" style="left:17px;top:203px"><svg width="22" height="22" viewBox="0 0 22 22" fill="#1b3f63"><rect x="5" y="1" width="12" height="20" rx="1"/><path d="M2 4h2v2H2zM2 9h2v2H2zM2 14h2v2H2zM18 4h2v2h-2zM18 9h2v2h-2zM18 14h2v2h-2z"/></svg>Working Memory</div>
    <ul class="abs word-list" style="left:55px;top:238px">
      <li>Cool Down</li><li>Crave</li><li>Fo for</li><li>Go To</li><li>In The Mood For</li><li>Sip</li><li>Soothing</li><li>Stick With</li><li>Throw In/Throw On</li>
    </ul>
    <div class="abs group-title" style="left:17px;top:522px"><svg width="20" height="22" viewBox="0 0 20 22" fill="#1b3f63"><path d="M5 9V6a5 5 0 0 1 10 0v3h-2.5V6a2.5 2.5 0 0 0-5 0v3z"/><rect x="3" y="9" width="14" height="11" rx="1"/></svg>Long-Term Memory</div>
    <div class="abs word" style="left:52px;top:561px">Give It A Try</div>
  </aside>

  <div class="abs word-head" style="left:529px;top:110px">GRAB <svg width="20" height="20" viewBox="0 0 20 20" fill="#f5b700"><path d="M10 1l2.8 5.8 6.2.8-4.6 4.3 1.2 6.2L10 15l-5.6 3.1 1.2-6.2L1 7.6l6.2-.8z"/></svg></div>
  <div class="abs start-btn"><svg width="17" height="17" viewBox="0 0 18 18"><circle cx="9" cy="9" r="9" fill="#fff"/><path d="M7 5l6 4-6 4z" fill="#1b3f63"/></svg>Start Vocabulary Review Exercise 3</div>
  <p class="abs para" style="left:529px;top:186px">The Word "Grab" Is Most Commonly Used As A Verb, Meaning To Take Something Quickly Or Suddenly. Imagine You're Running Late For School. You Don't Have Time For Breakfast, So You Quickly Grab An Apple From The Kitchen And Rush Out The Door. As You Reach The Bus Stop, Your Friend Waves And Says, "Hey! Let's Grab A Coffee Aller Class" Later, When You Sit Down, Your Phone Starts Ringing. You Grab It From Your Brag And Answer</p>

  <svg class="abs chart" style="top:374px" width="920" height="270" viewBox="600 510 920 270" font-family="Roboto, sans-serif" font-size="10" fill="#333" text-anchor="middle">
    <path d="M628 560V773H1490" fill="none" stroke="#e6e6e6"/>
    <rect x="654" y="563" width="18" height="210" fill="var(--bar-blue)"/><rect x="683" y="585" width="18" height="188" fill="var(--bar-green)"/>
    <rect x="735" y="585" width="18" height="188" fill="var(--bar-gray)"/><rect x="764" y="606" width="18" height="167" fill="var(--bar-yellow)"/>
    <rect x="816" y="667" width="18" height="106" fill="var(--bar-blue)"/><rect x="845" y="602" width="18" height="171" fill="var(--bar-green)"/>
    <rect x="898" y="563" width="18" height="210" fill="var(--bar-yellow)"/><rect x="927" y="648" width="18" height="125" fill="var(--bar-gray)"/>
    <rect x="979" y="563" width="18" height="210" fill="var(--bar-blue)"/><rect x="1008" y="585" width="18" height="188" fill="var(--bar-gray)"/>
    <rect x="1060" y="648" width="18" height="125" fill="var(--bar-green)"/><rect x="1089" y="617" width="18" height="156" fill="var(--bar-yellow)"/>
    <text x="1068" y="625">23</text><text x="1068" y="639">May</text><text x="1096" y="611">12:00</text>
    <rect x="1135" y="667" width="18" height="106" fill="var(--bar-blue)"/><rect x="1164" y="563" width="18" height="210" fill="var(--bar-green)"/>
    <text x="1144" y="646">24</text><text x="1144" y="660">May</text><text x="1173" y="555">12:00</text>
    <rect x="1208" y="563" width="18" height="210" fill="var(--bar-blue)"/><rect x="1237" y="624" width="18" height="149" fill="var(--bar-yellow)"/>
    <text x="1217" y="540">25</text><text x="1217" y="554">May</text><text x="1246" y="618">12:00</text>
    <rect x="1289" y="648" width="18" height="125" fill="var(--bar-gray)"/><rect x="1318" y="617" width="18" height="156" fill="var(--bar-green)"/>
    <text x="1298" y="626">26</text><text x="1298" y="640">May</text><text x="1327" y="610">12:00</text>
    <rect x="1364" y="667" width="18" height="106" fill="var(--bar-yellow)"/><rect x="1393" y="563" width="18" height="210" fill="var(--bar-gray)"/>
    <text x="1373" y="647">27</text><text x="1373" y="661">May</text><text x="1402" y="558">12:00</text>
    <rect x="1435" y="602" width="18" height="171" fill="var(--bar-green)"/><rect x="1464" y="667" width="18" height="106" fill="var(--bar-yellow)"/>
    <text x="1444" y="581">28</text><text x="1444" y="595">May</text><text x="1473" y="662">12:00</text>
  </svg>
  <div class="abs legend" style="top:666px">
    <span><i style="background:var(--bar-blue)"></i>Long Term Memory</span>
    <span><i style="background:var(--bar-green)"></i>Working Memory</span>
    <span><i style="background:var(--bar-yellow)"></i>Short Term Memory</span>
    <span><i style="background:var(--bar-gray)"></i>Forgotten Memory</span>
  </div>
  <div class="abs section-title" style="left:528px;top:752px">WORDWISE TUTOR LEAMING ANALYSIS</div>
  <p class="abs para" style="left:529px;top:790px">Lorem ipsum dolor sit amet, consectetur adipiscing elit, sed do eiusmod tempor incididunt ut labore et dolore magna aliqua. Ut enim ad minim veniam, quis nostrud exercitation ullamco laboris nisi ut aliquip</p>

  <div class="abs dim"></div>
  <div class="abs close">X</div>
  <div class="abs modal">
    <div class="abs select" style="left:28px;top:31px;width:409px;height:42px">All <span>⌄</span></div>
    <div class="abs group-title" style="left:28px;top:108px"><svg width="22" height="22" viewBox="0 0 22 22" fill="none" stroke="#1b3f63" stroke-width="2.2"><path d="M3 11a8 8 0 1 0 2.5-5.8L3 7.5M3 3v4.5h4.5M11 7v4l3 2"/></svg>Short-Term Memory</div>
    <div class="abs word" style="left:64px;top:148px">Grab</div>
    <div class="abs group-title" style="left:30px;top:196px"><svg width="20" height="22" viewBox="0 0 20 22" fill="#1b3f63"><path d="M5 9V6a5 5 0 0 1 10 0v3h-2.5V6a2.5 2.5 0 0 0-5 0v3z"/><rect x="3" y="9" width="14" height="11" rx="1"/></svg>Long-Term Memory</div>
    <div class="abs word" style="left:64px;top:237px">Give It A Try</div>
    <div class="abs group-title" style="left:258px;top:106px"><svg width="22" height="22" viewBox="0 0 22 22" fill="#1b3f63"><rect x="5" y="1" width="12" height="20" rx="1"/><path d="M2 4h2v2H2zM2 9h2v2H2zM2 14h2v2H2zM18 4h2v2h-2zM18 9h2v2h-2zM18 14h2v2h-2z"/></svg>Working Memory</div>
    <ul class="abs word-list" style="left:297px;top:143px">
      <li>Cool Down</li><li>Crave</li><li>Fo for</li><li>Go To</li><li>In The Mood For</li><li>Sip</li><li>Soothing</li><li>Stick With</li><li>Throw In/Throw On</li>
    </ul>
  </div>
</section>

</div>
</body>
</html>
```